Dental specialist needs a sharp looking letterhead

I am looking for a letterhead to be used to send letters and communication between myself (a dental specialist) and other dentists.
My office is a state of the art dental specialty office.
I need to letterhead to also state:
Bertram L. Oswick DDS
2748 Tollard Avenue, Suite K
West Tollard, NY 14391
(716)392-5061
fax: (716)392-5087
oswickroot.com (**this email address may change)

i included my logo designs.
thank you

Target Market(s)

dentists

Industry/Entity Type

Communication

Requirements
Must have
• the included logo, whether the vertical or horizontal versions

```html
<!DOCTYPE html>
<html lang="en">
<head>
<meta charset="utf-8">
<title>Keystone Endodontics Letterhead</title>
<link href="https://fonts.googleapis.com/css2?family=Open+Sans:wght@400;600;700&display=swap" rel="stylesheet">
<style>
  :root {
    --backdrop: #9a9a9a;
    --paper: #ffffff;
    --ink: #3a3a3a;
    --brand-dark: #2b2f33;
    --brand-blue: #27a6e6;
    --band-top: #43b8f1;
    --band-bottom: #1f9ee0;
    --accent-green: #8cc63f;
  }
  * { box-sizing: border-box; margin: 0; padding: 0; }
  html, body {
    width: 1200px; height: 916px; overflow: hidden;
    background: var(--backdrop);
    font-family: "Open Sans", Arial, sans-serif;
  }
  .letterhead {
    position: absolute; left: 260px; top: 18px;
    width: 680px; height: 880px;
    background: var(--paper);
    box-shadow: 0 6px 24px rgba(0,0,0,0.25);
  }
  .brand {
    position: absolute; left: 44px; top: 44px;
  }
  .brand-name {
    display: flex; align-items: center; gap: 8px;
    font-size: 17px; font-weight: 700; color: var(--brand-dark);
    letter-spacing: 0.5px;
  }
  .brand-dot {
    width: 20px; height: 20px; border-radius: 50%;
    background: var(--brand-blue);
  }
  .doctor {
    margin: 6px 0 0 28px;
    font-size: 12px; color: var(--brand-blue); letter-spacing: 2px;
  }
  .doctor .credential {
    display: block; text-align: right;
    font-size: 9px; color: var(--accent-green); letter-spacing: 1.5px;
  }
  .letter-body {
    position: absolute; left: 230px; top: 150px; width: 400px;
    font-size: 8.5px; line-height: 1.5; color: var(--ink);
  }
  .letter-body p { margin-bottom: 10px; }
  .sign-off { margin-top: 56px; padding-left: 90px; }
  .contact-band {
    position: absolute; left: 0; right: 0; bottom: 86px; height: 34px;
    background: linear-gradient(var(--band-top), var(--band-bottom));
    color: #fff; font-size: 12.5px;
    display: flex; align-items: center; justify-content: center;
  }
  .contact-band .sep { margin: 0 8px; }
  .website {
    position: absolute; left: 0; right: 0; bottom: 56px;
    text-align: center; font-size: 13px; letter-spacing: 5px;
    color: var(--brand-dark); font-weight: 600;
  }
</style>
</head>
<body>
  <main class="letterhead">
    <header class="brand">
      <div class="brand-name"><span class="brand-dot"></span>KEYSTONE ENDODONTICS P.C.</div>
      <div class="doctor">Bertram L. Oswick<span class="credential">D.D.S</span></div>
    </header>

    <section class="letter-body">
      <p>Lorem Ipsum,</p>
      <p>Lorem ipsum dolor sit amet, consectetuer adipiscing elit. Nam cursus. Morbi ut mi. Nullam enim leo, egestas id, condimentum at, laoreet mattis, massa. Sed eleifend nonummy diam. Praesent mauris ante, elementum et, bibendum at, posuere sit amet, nibh. Duis tincidunt lectus quis dui viverra vestibulum. Suspendisse vulputate aliquam dui. Nulla elementum dui ut augue.</p>
      <p>Aliquam vehicula mi at mauris. Maecenas placerat, nisl at consequat rhoncus, sem nunc gravida justo, quis eleifend arcu velit quis lacus. Morbi magna magna, tincidunt a, mattis non, imperdiet vitae, tellus.</p>
      <p>Mauris nunc quam, venenatis nec, euismod sit amet, egestas placerat, est. Pellentesque habitant morbi tristique senectus et netus et malesuada fames ac turpis egestas. Cras id elit. Integer quis urna.</p>
      <p>Aliquam vehicula mi at mauris. Maecenas placerat, nisl at consequat rhoncus, sem nunc gravida justo, quis eleifend arcu velit quis lacus. Morbi magna magna, tincidunt a, mattis non, imperdiet vitae, tellus.</p>
      <p>Mauris nunc quam, venenatis nec, euismod sit amet, egestas placerat, est. Pellentesque habitant morbi tristique senectus et netus et malesuada fames ac turpis egestas. Cras id elit. Integer quis urna.</p>
      <p class="sign-off">Sincerly,</p>
    </section>

    <footer>
      <div class="contact-band">
        Address: 2748 Tollard Avenue, Suite K West Tollard, NY 14391<span class="sep">|</span>Phone: (716)392-5061<span class="sep">|</span>Fax: (716)392-5087
      </div>
      <div class="website">www.oswickroot.com</div>
    </footer>
  </main>
</body>
</html>
```